New Innovative Counselling and psychotherapy Service needs Business Card design

Keep it simple and professional. On one side, just company name and logo (perhaps in all blue) and maybe a tag line.

On other side (all white) my name and Qualifications in centre

Industry/Entity Type

Health And Wellness

Contact Information for Business Card

Dara Whelby
Counsellor & Psychotherapist
BSc (Psychol.), BA, Dip. (Couns. & Psych.), PG.Cert (CBT), FGTrK, ONRE

I will also require Mobile no, Email and web site address of which I'll pass on to final designer.

Font styles to use
Sans Serif

Requirements
Must have
• My Logo Only and please use the colours in logo that is in it.
Should not have
• Any other images

```html
<!DOCTYPE html>
<html lang="en">
<head>
<meta charset="utf-8">
<title>Thrive Lane – Business Card</title>
<link rel="stylesheet" href="https://fonts.googleapis.com/css2?family=Arimo:wght@400;700&family=Raleway:wght@400;500&display=swap">
<style>
  :root {
    --backdrop: #c6c6c6;
    --card-white: #f4f4f4;
    --card-dark: #333333;
    --brand-blue: #45b3ec;
    --brand-green: #96d35f;
    --ink: #3a3a3a;
    --ink-soft: #555555;
    --rule: #9a9a9a;
    --white: #ffffff;
  }
  * { margin: 0; padding: 0; box-sizing: border-box; }
  html, body { width: 1200px; height: 960px; overflow: hidden; }
  body {
    position: relative;
    background: var(--backdrop);
    font-family: "Arimo", Arial, sans-serif;
  }
  .card {
    position: absolute;
    width: 599px;
    height: 342px;
    border-radius: 16px;
    overflow: hidden;
  }
  .card--front { left: 322px; top: 110px; background: var(--card-white); }
  .card--back { left: 321px; top: 493px; background: var(--card-dark); }

  .brand {
    position: absolute;
    right: 26px;
    top: 33px;
    display: flex;
    align-items: center;
    gap: 14px;
  }
  .brand__dot {
    width: 54px; height: 54px; border-radius: 50%;
    background: var(--brand-blue);
  }
  .brand__name {
    font-family: "Arimo", Arial, sans-serif;
    font-size: 28px;
    color: var(--ink);
    font-weight: 400;
  }

  .person { position: absolute; left: 31px; top: 176px; width: 540px; }
  .person__name {
    font-size: 24px; font-weight: 700; color: var(--brand-blue);
    line-height: 28px;
  }
  .person__role { font-size: 15px; color: var(--ink-soft); line-height: 20px; margin-top: 2px; }
  .person__quals { font-size: 11px; color: var(--ink-soft); line-height: 14px; margin-top: 1px; }
  .person__rule { height: 1px; background: var(--rule); margin-top: 14px; width: 538px; }

  .contact { position: absolute; left: 32px; top: 264px; font-size: 14px; color: var(--ink); }
  .contact__row { display: flex; align-items: center; gap: 7px; height: 20px; }
  .contact__row svg { width: 13px; height: 13px; flex: none; }

  .footer-band { position: absolute; left: 0; bottom: 0; width: 599px; height: 30px; }
  .footer-band__url {
    position: absolute; left: 31px; bottom: 6px;
    font-size: 14px; letter-spacing: 1.2px; color: var(--white);
  }

  .back-mark {
    position: absolute; left: 0; top: 56px; width: 100%;
    display: flex; flex-direction: column; align-items: center; gap: 16px;
  }
  .back-mark__dot { width: 140px; height: 140px; border-radius: 50%; background: var(--brand-blue); }
  .back-mark__name { font-size: 24px; color: var(--white); }
  .tagline {
    position: absolute; left: 0; top: 289px; width: 100%;
    text-align: center; font-size: 14px; color: var(--white);
  }
</style>
</head>
<body>

<section class="card card--front">
  <div class="brand">
    <div class="brand__dot"></div>
    <span class="brand__name">Thrive Lane</span>
  </div>

  <div class="person">
    <h1 class="person__name">Dara Whelby</h1>
    <p class="person__role">Counsellor &amp; Psychotherapist</p>
    <p class="person__quals">BSc (Psychol.), BA, Dip. (Couns. &amp; Psych.) PG.Cert (CBT), FGTrK,</p>
    <div class="person__rule"></div>
  </div>

  <div class="contact">
    <div class="contact__row">
      <svg viewBox="0 0 13 13" aria-hidden="true"><rect x="3" y="0.5" width="7" height="12" rx="1.2" fill="none" stroke="var(--brand-blue)" stroke-width="1.4"/><rect x="4.6" y="2.2" width="3.8" height="7" fill="var(--brand-blue)"/></svg>
      <span>555 201 7730</span>
    </div>
    <div class="contact__row">
      <svg viewBox="0 0 13 13" aria-hidden="true"><rect x="0.5" y="3" width="12" height="8" fill="var(--brand-blue)"/><path d="M0.5 3 L6.5 7.5 L12.5 3" fill="none" stroke="var(--white)" stroke-width="1"/></svg>
      <span>dara@Thrivelane.com</span>
    </div>
  </div>

  <div class="footer-band">
    <svg width="599" height="30" viewBox="0 0 599 30" aria-hidden="true">
      <polygon points="258,12 599,12 599,24 270,24" fill="var(--brand-green)"/>
      <polygon points="0,0 248,0 274,24 599,24 599,30 0,30" fill="var(--brand-blue)"/>
    </svg>
    <span class="footer-band__url">www.Thrivelane.com</span>
  </div>
</section>

<section class="card card--back">
  <div class="back-mark">
    <div class="back-mark__dot"></div>
    <span class="back-mark__name">Thrive Lane</span>
  </div>
  <p class="tagline">Caring For Your Psychological Well-Being Is Our Top Priority</p>
</section>

</body>
</html>
```